Designer Instructions – Updated Referral Program Flyer

(Based on the mock-up in “Brief Layout and Instructions.pdf”)

OVERALL STYLE + LAYOUT

Maintain the same general layout, structure, and flow as the mock-up flyer (front and back).

This is an update of an older flyer, not a full redesign — keep the same sections, proportions, and overall visual feel, but with cleaner, more modern design improvements.

The final flyer should look clean, bold, professional, and high-impact, geared toward realtors, property managers, and contractors who refer work.

FRONT SIDE INSTRUCTIONS
1. Header Section

Remove the Rebuild Harbor Crest logo from the top banner.
(Shown on page 1 of the PDF)

2. Main Headline

Keep the same three-line structure:
EARN
UNLIMITED
CASH

Center it, maximize impact, and increase the font size of CASH so all three words match in importance.

Make the headline bold, clean, and the main focal point.

3. Cash Incentive Box

Keep the "$500 minimum OR 10% per referral" box, but upgrade the graphics to look sharper and more modern.

Ensure the wording matches exactly what’s in the mock-up.

4. Premier Partner Program Ribbon

Clean up and modernize the "PREMIER PARTNER PROGRAM" bar while keeping the same position and structure.

Ensure the checkmark badge remains crisp and professional.

5. Supporting Icons Section

Keep the four icons/benefit boxes (Guaranteed Payout, Free Evaluations, Affordable Solutions, Industry Leaders) in the same order.

Update the icons to cleaner, more modern styles — but maintain the same meanings.

Improve alignment and spacing for sharper visual consistency.

6. Remove Icons in Contact Area

At the bottom (“CALL TEXT OR BOOK ONLINE 858-471-6093 BrightlaneRenovate.com”), remove the phone and internet icons, as noted on page 2 of the PDF.

7. Replace All Images

I (Dorian) will provide all updated stock images separately via email.

Replace the flood/water-damage imagery and roof leak with the new images I send.

Keep image placement and proportions the same as the mock-up.

BACK SIDE INSTRUCTIONS
1. Header Image + “REFER / EARN” Section

Maintain the same large split-image layout (“The more you refer, the more you earn”).

Replace all background imagery with the new assets I will send.

Keep the CASH FLOW image section but modernize the type and spacing.

2. “HOW IT WORKS” Section

Preserve the three-column layout:

Refer Flood, Water & Mold Damage

We Take Care of Everything (evaluations/insurance)

Get Paid to Share

Update images, tighten spacing, and use modern iconography.

3. Remove Phone/Internet Icons

Same as the front side — remove small communication icons and keep only the text/number/URL.

4. Bottom Contact Bar

Keep the blue bar, same wording, same layout — just modernize the style if needed for clarity.

5. Replace All Back-Side Images

Again, I will email you the image assets.

Keep the layout EXACT — just update with higher-quality photos and improved design.

TEXT CONTENT (Keep as-is unless spacing adjustments needed)

All text shown in the PDF should remain exactly the same unless spacing or visual balance requires minor adjustments.
Example from page 3:

“REFER FLOOD, MOLD & CONSTRUCTION JOBS”

“We Schedule a Free Estimate. If Approved, You Get Paid.”

“Everybody Benefits From Referrals”

Everything stays, just refreshed and visually improved.

DESIGN GOALS

Flyer should look high-end and trustworthy, not salesy.

Consistent color theme: blues, whites, yellows, same palette as original.

Use bold, modern fonts with strong readability.

Ensure all headlines pop and all benefit boxes are clean, well-aligned, and evenly spaced.

The final result should feel like a premium referral program flyer for a top-tier restoration/remodel company.

FILES I WILL PROVIDE

I will send the designer:

All replacement stock photos

Any updated logos (if needed)

Original high-resolution version of the mock-up (if available)

Any additional icons preferred

Colors
0054AA
0677BA
7BADD7
CADEEF
E8F1F8

Requirements
Must have
• Designer Instructions – Updated Referral Program Flyer (Based on the mock-up in “Brief Layout and Instructions.pdf”) OVERALL STYLE + LAYOUT Maintain the same general layout, structure, and flow as the mock-up flyer (front and back). This is an update of an older flyer, not a full redesign — keep the same sections, proportions, and overall visual feel, but with cleaner, more modern design improvements. The final flyer should look clean, bold, professional, and high-impact, geared toward realtors, property managers, and contractors who refer work. FRONT SIDE INSTRUCTIONS 1. Header Section Remove the Rebuild Harbor Crest logo from the top banner. (Shown on page 1 of the PDF) 2. Main Headline Keep the same three-line structure: EARN UNLIMITED CASH Center it, maximize impact, and increase the font size of CASH so all three words match in importance. Make the headline bold, clean, and the main focal point. 3. Cash Incentive Box Keep the "$500 minimum OR 10% per referral" box, but upgrade the graphics to look sharper and more modern. Ensure the wording matches exactly what’s in the mock-up. 4. Premier Partner Program Ribbon Clean up and modernize the "PREMIER PARTNER PROGRAM" bar while keeping the same position and structure. Ensure the checkmark badge remains crisp and professional. 5. Supporting Icons Section Keep the four icons/benefit boxes (Guaranteed Payout, Free Evaluations, Affordable Solutions, Industry Leaders) in the same order. Update the icons to cleaner, more modern styles — but maintain the same meanings. Improve alignment and spacing for sharper visual consistency. 6. Remove Icons in Contact Area At the bottom (“CALL TEXT OR BOOK ONLINE 858-471-6093 BrightlaneRenovate.com”), remove the phone and internet icons, as noted on page 2 of the PDF. 7. Replace All Images I (Dorian) will provide all updated stock images separately via email. Replace the flood/water-damage imagery and roof leak with the new images I send. Keep image placement and proportions the same as the mock-up. BACK SIDE INSTRUCTIONS 1. Header Image + “REFER / EARN” Section Maintain the same large split-image layout (“The more you refer, the more you earn”). Replace all background imagery with the new assets I will send. Keep the CASH FLOW image section but modernize the type and spacing. 2. “HOW IT WORKS” Section Preserve the three-column layout: Refer Flood, Water & Mold Damage We Take Care of Everything (evaluations/insurance) Get Paid to Share Update images, tighten spacing, and use modern iconography. 3. Remove Phone/Internet Icons Same as the front side — remove small communication icons and keep only the text/number/URL. 4. Bottom Contact Bar Keep the blue bar, same wording, same layout — just modernize the style if needed for clarity. 5. Replace All Back-Side Images Again, I will email you the image assets. Keep the layout EXACT — just update with higher-quality photos and improved design. TEXT CONTENT (Keep as-is unless spacing adjustments needed) All text shown in the PDF should remain exactly the same unless spacing or visual balance requires minor adjustments. Example from page 3: “REFER FLOOD, MOLD & CONSTRUCTION JOBS” “We Schedule a Free Estimate. If Approved, You Get Paid.” “Everybody Benefits From Referrals” Everything stays, just refreshed and visually improved. DESIGN GOALS Flyer should look high-end and trustworthy, not salesy. Consistent color theme: blues, whites, yellows, same palette as original. Use bold, modern fonts with strong readability. Ensure all headlines pop and all benefit boxes are clean, well-aligned, and evenly spaced. The final result should feel like a premium referral program flyer for a top-tier restoration/remodel company. FILES I WILL PROVIDE I will send the designer: All replacement stock photos Any updated logos (if needed) Original high-resolution version of the mock-up (if available) Any additional icons preferred

```html
<!DOCTYPE html>
<html lang="en">
<head>
<meta charset="utf-8">
<title>Referral Program Flyer – Front and Back</title>
<link href="https://fonts.googleapis.com/css2?family=Poppins:wght@400;500;600;700;800;900&display=swap" rel="stylesheet">
<style>
  :root{
    --navy:#14306f;
    --blue:#0054aa;
    --blue-mid:#0677ba;
    --blue-soft:#7badd7;
    --blue-pale:#cadeef;
    --blue-mist:#e8f1f8;
    --red:#c4161c;
    --yellow:#fde021;
    --ink:#1a1a1a;
    --body:#333;
    --stage:#8f8f8f;
    --grey-band:#e4e6ea;
  }
  *{box-sizing:border-box;margin:0;padding:0}
  html,body{width:1200px;height:442px;overflow:hidden}
  body{background:var(--stage);font-family:"Poppins",sans-serif;position:relative;color:var(--ink)}
  .card{position:absolute;top:47px;width:537px;height:348px;background:#fff;overflow:hidden;box-shadow:0 3px 8px rgba(0,0,0,.25)}
  .card--front{left:48px}
  .card--back{left:615px}
  .abs{position:absolute}

  /* front header */
  .front-header{left:0;top:0;width:537px;height:126px}
  .headline{left:0;top:4px;width:305px;text-align:center;color:#fff;font-weight:800;line-height:1}
  .headline__earn{display:block;color:var(--yellow);font-size:40px;letter-spacing:1px}
  .headline__unlimited{display:block;font-size:19px;margin-top:3px}
  .headline__cash{display:block;color:var(--yellow);font-size:42px;margin-top:3px;letter-spacing:1px}
  .headline__sub{display:block;font-size:10.5px;font-weight:500;margin-top:3px}

  /* incentive pills */
  .incentive{left:50px;top:134px;width:206px;height:32px}
  .pill{position:absolute;top:0;height:32px;background:var(--red);color:#fff;border-radius:16px;font-weight:700}
  .pill--min{left:0;width:80px;text-align:center;line-height:1}
  .pill--min b{display:block;font-size:11.5px;margin-top:5px}
  .pill--min span{display:block;font-size:7.5px;font-weight:600;margin-top:1px}
  .pill--pct{left:96px;width:110px;display:flex;align-items:center;padding-left:16px;gap:4px}
  .pill--pct b{font-size:17px}
  .pill--pct span{font-size:7px;line-height:1.05;font-weight:600}
  .pill--pct span em{font-style:normal;font-size:10px;font-weight:700;display:block}
  .or-badge{position:absolute;left:69px;top:-2px;width:36px;height:36px;border-radius:50%;background:#fff;color:var(--navy);font-weight:800;font-size:10px;display:flex;align-items:center;justify-content:center}

  /* partner ribbon */
  .ribbon{left:306px;top:137px;width:217px;height:24px}
  .ribbon__premier{position:absolute;left:103px;top:-6px;transform:translateX(-50%);font-size:5px;font-weight:700;color:var(--navy)}
  .ribbon__left{position:absolute;left:0;top:0;width:103px;height:24px;background:var(--red);color:#fff;font-weight:700;font-size:10px;line-height:24px;padding-left:31px}
  .ribbon__right{position:absolute;left:103px;top:0;width:114px;height:24px;background:var(--yellow);color:var(--navy);font-weight:700;font-size:10px;line-height:24px;padding-left:27px}
  .ribbon__badge{position:absolute;left:91px;top:-1px;width:26px;height:26px}

  .tagline{left:0;top:175px;width:537px;text-align:center;font-size:10.5px;font-weight:700;color:var(--ink)}

  /* benefits */
  .benefit{position:absolute;top:193px;width:111px;height:106px}
  .benefit__frame{position:absolute;inset:0}
  .benefit__title{position:absolute;left:0;top:10px;width:111px;text-align:center;font-size:7.6px;font-weight:700;line-height:1.6;color:var(--ink)}
  .benefit__text{position:absolute;left:10px;top:61px;width:72px;font-size:6.8px;line-height:10.6px;color:var(--body);white-space:nowrap}
  .benefit__text b{font-weight:700;color:var(--ink)}
  .benefit__icon{position:absolute;left:84px;top:62px;width:26px;height:26px}

  /* contact bar */
  .contact{left:0;top:320px;width:537px;height:28px}
  .contact__text{top:320px;line-height:28px;font-weight:700;font-size:10.5px}
  .contact__call{left:39px;color:#fff}
  .contact__phone{left:234px;color:var(--ink)}
  .contact__web{left:347px;color:var(--ink)}

  /* back header */
  .badge-24{left:96px;top:10px;width:108px;height:108px;border-radius:50%;background:var(--red);box-shadow:0 0 0 3px #fff}
  .tiles{left:350px;top:36px;width:116px;height:68px;border-radius:4px;background:#8fd8da}

  .how{left:0;top:126px;width:240px;height:31px}
  .how__label{left:52px;top:126px;line-height:31px;font-size:15.5px;font-weight:800;color:var(--navy)}

  .step{position:absolute;top:169px;width:154px;height:132px;border:2px solid var(--navy);border-radius:7px;background:#fff}
  .step__photo{position:absolute;left:6px;top:6px;width:138px;height:72px;border-radius:4px}
  .step__title{position:absolute;left:8px;top:82px;width:140px;font-size:6.8px;font-weight:700;line-height:1.25;color:var(--ink)}
  .step__text{position:absolute;left:8px;top:104px;width:140px;font-size:7px;line-height:1.5;color:var(--body)}

  .refer-note{left:0;top:307px;width:537px;text-align:center;font-size:7px;font-weight:700;color:var(--navy)}
</style>
</head>
<body>

<section class="card card--front" aria-label="Referral flyer front">
  <svg class="abs front-header" viewBox="0 0 537 126" aria-hidden="true">
    <defs>
      <linearGradient id="kitchenTone" x1="0" y1="0" x2="1" y2="1">
        <stop offset="0" stop-color="#e9ecef"/><stop offset=".5" stop-color="#c9d3dc"/><stop offset="1" stop-color="#f2f2f0"/>
      </linearGradient>
      <linearGradient id="skylineTone" x1="0" y1="0" x2="0" y2="1">
        <stop offset="0" stop-color="#1b3a86"/><stop offset="1" stop-color="#112e6b"/>
      </linearGradient>
    </defs>
    <rect width="537" height="126" fill="url(#kitchenTone)"/>
    <polygon points="0,0 297,0 273,62 302,126 0,126" fill="url(#skylineTone)"/>
    <polyline points="297,0 273,62 302,126" fill="none" stroke="#fff" stroke-width="3"/>
  </svg>
  <div class="abs" role="img" aria-label="Bright white remodeled kitchen with sink and window" style="left:305px;top:0;width:232px;height:126px"></div>
  <div class="abs" role="img" aria-label="Faint city skyline behind headline" style="left:0;top:0;width:270px;height:126px"></div>

  <h1 class="abs headline">
    <span class="headline__earn">EARN</span>
    <span class="headline__unlimited">UNLIMITED</span>
    <span class="headline__cash">CASH</span>
    <span class="headline__sub">GET PAID TOREFER A FLOOD</span>
  </h1>

  <div class="abs incentive">
    <div class="pill pill--min"><b>$500</b><span>Minimum</span></div>
    <div class="pill pill--pct"><b>10%</b><span><em>Per</em>Referral!</span></div>
    <div class="or-badge">OR</div>
  </div>

  <div class="abs ribbon">
    <span class="ribbon__premier">PREMIER</span>
    <div class="ribbon__left">PARTNER</div>
    <div class="ribbon__right">PROGRAM</div>
    <svg class="ribbon__badge" viewBox="0 0 26 26" aria-hidden="true">
      <circle cx="13" cy="13" r="13" fill="var(--navy)"/>
      <path d="M13 5.5l6 2.3v4.4c0 4-2.6 6.7-6 8.2-3.4-1.5-6-4.2-6-8.2V7.8z" fill="#fff"/>
      <path d="M10 12.8l2.2 2.2 4-4.2" fill="none" stroke="var(--navy)" stroke-width="1.8" stroke-linecap="round" stroke-linejoin="round"/>
    </svg>
  </div>

  <p class="abs tagline">PARTNER WITH US &amp; EVERYBODY WINS!</p>

  <div class="benefit" style="left:30px">
    <svg class="benefit__frame" viewBox="0 0 111 106" aria-hidden="true">
      <path d="M2 104 V60 M2 104 H100" fill="none" stroke="var(--navy)" stroke-width="1.6"/>
      <circle cx="100" cy="104" r="1.8" fill="var(--navy)"/>
      <rect x="2" y="1" width="107" height="44" rx="22" fill="#fff" stroke="var(--navy)" stroke-width="3.5"/>
    </svg>
    <p class="benefit__title">GUARANTEED<br>PAYOUT</p>
    <p class="benefit__text">Minimum <b>$500</b> or<br><b>10%</b> of Total Invoice<br>Paid Fast</p>
    <svg class="benefit__icon" viewBox="0 0 28 28" aria-hidden="true" fill="none" stroke="#222" stroke-width="1.1">
      <path d="M14 2l3 2.2 3.6-.3 1.2 3.4 3 2-1.1 3.5 1.1 3.5-3 2-1.2 3.4-3.6-.3L14 23l-3-2.2-3.6.3-1.2-3.4-3-2L4.3 12 3.2 8.5l3-2L7.4 3.1l3.6.3z"/>
      <circle cx="14" cy="12.5" r="6"/>
      <path d="M11.3 12.6l2 2 3.6-3.8"/>
      <path d="M8 21l-2 6 3-1.5 1.5 2.5 2-5M20 21l2 6-3-1.5-1.5 2.5-2-5"/>
    </svg>
  </div>

  <div class="benefit" style="left:150px">
    <svg class="benefit__frame" viewBox="0 0 111 106" aria-hidden="true">
      <path d="M2 104 V60 M2 104 H100" fill="none" stroke="var(--navy)" stroke-width="1.6"/>
      <circle cx="100" cy="104" r="1.8" fill="var(--navy)"/>
      <rect x="2" y="1" width="107" height="44" rx="22" fill="#fff" stroke="var(--navy)" stroke-width="3.5"/>
    </svg>
    <p class="benefit__title">FREE<br>ESTIMATES</p>
    <p class="benefit__text">Fast &amp; Free<br>Inspections &amp;<br>Written Estimates</p>
    <svg class="benefit__icon" viewBox="0 0 28 28" aria-hidden="true" fill="none" stroke="#222" stroke-width="1.1">
      <rect x="4" y="2" width="18" height="23" rx="1"/>
      <path d="M8 6h2M8 10h10M8 13h10M8 16h10M8 20h6"/>
      <text x="12" y="9" font-size="5" fill="#222" stroke="none" font-family="Poppins,sans-serif">$</text>
      <circle cx="22" cy="22" r="4.5" fill="#fff"/>
      <path d="M20 22l1.5 1.5 2.8-2.8"/>
    </svg>
  </div>

  <div class="benefit" style="left:270px">
    <svg class="benefit__frame" viewBox="0 0 111 106" aria-hidden="true">
      <path d="M2 104 V60 M2 104 H100" fill="none" stroke="var(--navy)" stroke-width="1.6"/>
      <circle cx="100" cy="104" r="1.8" fill="var(--navy)"/>
      <rect x="2" y="1" width="107" height="44" rx="22" fill="#fff" stroke="var(--navy)" stroke-width="3.5"/>
    </svg>
    <p class="benefit__title">AFFORDABLE<br>SOLUTIONS</p>
    <p class="benefit__text">Lowest Out of Pocket<br>Costs for Your<br>Customers</p>
    <svg class="benefit__icon" viewBox="0 0 28 28" aria-hidden="true" fill="none" stroke="#222" stroke-width="1.1">
      <ellipse cx="9" cy="14" rx="6" ry="2"/><path d="M3 14v10c0 1.1 2.7 2 6 2s6-.9 6-2V14M3 17.5c0 1.1 2.7 2 6 2s6-.9 6-2M3 21c0 1.1 2.7 2 6 2s6-.9 6-2"/>
      <circle cx="20" cy="20" r="5.5" fill="#fff"/>
      <text x="17.8" y="22.5" font-size="7" fill="#222" stroke="none" font-family="Poppins,sans-serif">$</text>
      <path d="M20 12V2M17 5l3-3 3 3"/>
    </svg>
  </div>

  <div class="benefit" style="left:390px">
    <svg class="benefit__frame" viewBox="0 0 111 106" aria-hidden="true">
      <path d="M2 104 V60 M2 104 H100" fill="none" stroke="var(--navy)" stroke-width="1.6"/>
      <circle cx="100" cy="104" r="1.8" fill="var(--navy)"/>
      <rect x="2" y="1" width="107" height="44" rx="22" fill="#fff" stroke="var(--navy)" stroke-width="3.5"/>
    </svg>
    <p class="benefit__title">INDUSTRY<br>LEADERS</p>
    <p class="benefit__text">Licensed &amp; Certified<br>Experts Provide 100%<br>Guarantee</p>
    <svg class="benefit__icon" viewBox="0 0 28 28" aria-hidden="true" fill="none" stroke="#222" stroke-width="1.1">
      <rect x="7" y="2" width="14" height="11"/>
      <path d="M9 5h2v2H9zM13 5h2v2h-2zM17 5h2v2h-2zM9 9h2v2H9zM17 9h2v2h-2zM13 9h2v4h-2z"/>
      <path d="M3 13h22M5 13c0 6 4 10 9 10s9-4 9-10"/>
      <path d="M14 23v3M9 22l-2 3M19 22l2 3"/>
    </svg>
  </div>

  <svg class="abs contact" viewBox="0 0 537 28" aria-hidden="true">
    <rect width="537" height="28" fill="#fff"/>
    <polygon points="210,0 332,0 350,28 224,28" fill="var(--grey-band)"/>
    <polygon points="0,0 210,0 224,28 0,28" fill="var(--navy)"/>
    <polygon points="525,0 537,0 537,28" fill="var(--grey-band)"/>
  </svg>
  <span class="abs contact__text contact__call">CALL, TEXT OR BOOK ONLINE</span>
  <span class="abs contact__text contact__phone">858-471-6093</span>
  <span class="abs contact__text contact__web">www.BrightlaneRenovate.com</span>
</section>

<section class="card card--back" aria-label="Referral flyer back">
  <svg class="abs" viewBox="0 0 537 126" style="left:0;top:0;width:537px;height:126px" aria-hidden="true">
    <defs>
      <linearGradient id="duskTone" x1="0" y1="0" x2="0" y2="1">
        <stop offset="0" stop-color="#6d5a8c"/><stop offset=".45" stop-color="#a77790"/><stop offset=".62" stop-color="#3d3550"/><stop offset="1" stop-color="#4a4f6e"/>
      </linearGradient>
      <linearGradient id="moneyTone" x1="0" y1="0" x2="1" y2="1">
        <stop offset="0" stop-color="#e6e8e2"/><stop offset=".5" stop-color="#bfc4bc"/><stop offset="1" stop-color="#dcdfd8"/>
      </linearGradient>
    </defs>
    <rect width="537" height="126" fill="url(#moneyTone)"/>
    <polygon points="0,0 300,0 275,63 300,126 0,126" fill="url(#duskTone)"/>
    <polyline points="300,0 275,63 300,126" fill="none" stroke="#fff" stroke-width="3"/>
  </svg>
  <div class="abs" role="img" aria-label="Bay city skyline at dusk reflected on water" style="left:0;top:0;width:290px;height:126px"></div>
  <div class="abs" role="img" aria-label="Spread of hundred-dollar bills" style="left:300px;top:0;width:237px;height:126px"></div>

  <div class="abs badge-24" role="img" aria-label="Round red 24 hour emergency service emblem"></div>
  <div class="abs tiles" role="img" aria-label="Letter tiles spelling CASH FLOW lying on banknotes"></div>

  <svg class="abs how" viewBox="0 0 240 31" aria-hidden="true">
    <polygon points="0,0 215,0 236,31 0,31" fill="var(--yellow)"/>
  </svg>
  <h2 class="abs how__label">HOW IT WORKS</h2>

  <div class="step" style="left:29px">
    <div class="step__photo" role="img" aria-label="Drying fans and dehumidifiers in a water-damaged room" style="background:linear-gradient(135deg,#3f8fb5,#9db2b8 55%,#c9ccc9)"></div>
    <p class="step__title">REFER FLOOD, MOLD &amp;<br>CONSTRUCTION JOBS:</p>
    <p class="step__text">It’s Simple to Refer 24/7:<br>Call, Text or Book Online.</p>
  </div>
  <div class="step" style="left:189px">
    <div class="step__photo" role="img" aria-label="Inspector with clipboard in front of a house" style="background:linear-gradient(135deg,#7fa6c9,#d9dcd8 50%,#6f8f5a)"></div>
    <p class="step__title">WE TAKE CARE OF<br>EVERYTHING:</p>
    <p class="step__text">We Schedule a Free Estimate.<br>If Approved, You Get Paid.</p>
  </div>
  <div class="step" style="left:349px">
    <div class="step__photo" role="img" aria-label="Yellow road sign reading Get Paid to Share against blue sky" style="background:linear-gradient(90deg,#6fa3d6,#b9d3ea 45%,#f2d81c 70%,#7aaedb)"></div>
    <p class="step__title">EVERYBODY BENEFITS<br>FROM REFERRALS</p>
    <p class="step__text">We Provide Expert Quality<br>Work for Affordable Price.</p>
  </div>

  <p class="abs refer-note">REFER: FLOODS, REMODELS, RENOVATIONS &amp; REPAIRS</p>

  <svg class="abs contact" viewBox="0 0 537 28" aria-hidden="true">
    <rect width="537" height="28" fill="#fff"/>
    <polygon points="210,0 322,0 340,28 224,28" fill="var(--grey-band)"/>
    <polygon points="0,0 210,0 224,28 0,28" fill="var(--navy)"/>
    <polygon points="525,0 537,0 537,28" fill="var(--grey-band)"/>
  </svg>
  <span class="abs contact__text contact__call">CALL, TEXT OR BOOK ONLINE</span>
  <span class="abs contact__text contact__phone">858-471-6093</span>
  <span class="abs contact__text contact__web">www.BrightlaneRenovate.com</span>
</section>

</body>
</html>
```